Core Value Graphic for a Service Disabled and Minority Certified contractor

My company, Keystone Aid Partners, is a US Federal Contractor that hires veterans and service disabled veterans. Our website is www.keystoneaid7.example. We work hard to maintain a 50:50 split between veterans and non-veterans on our team. Our tagline is "To Find a Better Way." We are continually looking to integrate technology and efficiency into all that we do.

I want a way to express our company core values visually so that our employees and customers alike can read them and get a sense of who we are, what drives us to succeed, and what makes up our team DNA.

I need an artist like you to help me represent our core values visually. In a manner that I can print it out on an 8"X11" sheet of paper or a large 48" X 48" poster, without losing the visual clarity or that it pixelates out of focus. I am looking for a color scheme that is patriotic with Red, White, and Blues and similar hues. I would also like to incorporate my logo and tagline into the design in some manner.

I have attached several examples of a Core Value Grids from other companies. I am hopeful it will inspire you, and a get your brain juices flowing to provide me with a knockout Core Value Grid that will rock only you can provide! I also include a copy of my company Core Values and a copy of our Logo.

Looking forward to seeing your creations. Thanks.

Target Market(s)

Employees, any potential strategic alliance partners, and customers.

Industry/Entity Type

Contractor

Requirements
Must have
• Patriotic feel and have my logo someplace on the document.

```html
<!DOCTYPE html>
<html lang="en">
<head>
<meta charset="utf-8">
<title>Keystone Aid Partners — Core Values</title>
<link href="https://fonts.googleapis.com/css2?family=Montserrat:wght@800&family=Exo+2:wght@500;600&family=Roboto:wght@400&display=swap" rel="stylesheet">
<style>
  :root{
    --backdrop:#808080;
    --sheet:#f7f7f8;
    --red:#a11a33;
    --maroon:#6a0f20;
    --navy:#1b2a5e;
    --ink:#333;
    --label:#86162c;
    --frame:#24336b;
    --shadow:#1c1c1c;
  }
  *{box-sizing:border-box;margin:0;padding:0}
  html,body{width:1022px;height:1200px;overflow:hidden;background:var(--backdrop)}
  .sheet{position:absolute;left:174px;top:123px;width:674px;height:953px;background:var(--sheet);overflow:hidden;font-family:Roboto,Arial,sans-serif;color:var(--ink)}
  .title-banner{position:absolute;left:0;top:48px;width:360px;height:66px;background:linear-gradient(90deg,var(--maroon),var(--red) 45%,var(--maroon));clip-path:polygon(0 0,100% 0,96% 50%,100% 100%,0 100%);display:flex;align-items:center;padding-left:29px;font-family:Montserrat,sans-serif;font-weight:800;font-size:41px;color:#fff;letter-spacing:1px}
  .banner-shadow{position:absolute;left:216px;top:114px;width:144px;height:19px;background:var(--shadow);clip-path:polygon(20% 0,100% 0,100% 100%,0 100%)}
  .brand{position:absolute;left:440px;top:62px;display:flex;align-items:center;gap:8px;font-family:"Exo 2",sans-serif;font-weight:600;font-size:19px;color:var(--navy);line-height:1.1}
  .brand-mark{width:14px;height:14px;background:var(--red)}
  .tagline{position:absolute;left:216px;top:133px;width:458px;height:48px;background:var(--navy);color:#fff;font-family:Montserrat,sans-serif;font-weight:800;font-size:28px;letter-spacing:1.5px;display:flex;align-items:center;justify-content:center}
  .value{position:absolute;background:#fff;border:1.5px solid var(--frame);border-radius:6px;padding:8px 10px;font-size:8.6px;line-height:1.52;text-align:justify}
  .value h2{font-family:"Exo 2",sans-serif;font-weight:600;color:var(--maroon);font-size:20px;line-height:1.2;text-align:center;margin-bottom:10px}
  .value h2 em{font-style:normal;color:var(--red)}
  .value p{text-indent:10px}
  .value .lbl{color:var(--label)}
  .v1{left:42px;top:194px;width:291px;height:229px}
  .v2{left:342px;top:194px;width:290px;height:229px}
  .v2 h2{margin:7px 0 24px}
  .v3{left:42px;top:444px;width:348px;height:294px;font-size:9.2px}
  .v3 h2{text-align:left;margin-bottom:8px}
  .v4{left:415px;top:442px;width:218px;height:297px;font-size:9.2px;padding-top:6px}
  .v4 h2{text-align:left;font-size:19px;padding-left:12px}
  .v5{left:42px;top:749px;width:591px;height:133px;font-size:9.2px;padding:10px 15px}
  .v5 h2{margin-bottom:10px}
  .v5 p{text-indent:0;margin-bottom:3px}
  .gap{margin-top:4px}
  .float-r{float:right}
  .emblem{position:absolute;left:236px;top:367px;width:196px;height:196px;border-radius:50%;background:var(--navy);color:#fff;font-family:Montserrat,sans-serif;font-weight:800;font-size:33px;line-height:1.05;text-align:center;padding-top:50px;z-index:3}
  .sweep{position:absolute;left:0;top:0;width:674px;height:953px;z-index:2;pointer-events:none}
  .footer{position:absolute;left:0;bottom:0;width:674px;height:44px;background:linear-gradient(90deg,var(--maroon),var(--red) 50%,var(--maroon));color:#fff;font-size:14px;display:flex;align-items:center;justify-content:center;letter-spacing:.3px}
</style>
</head>
<body>
<main class="sheet">
  <div class="banner-shadow"></div>
  <h1 class="title-banner">CORE VALUES</h1>
  <div class="brand"><span class="brand-mark"></span><span>KEYSTONE AID<br>PARTNERS</span></div>
  <div class="tagline">TO FIND A BETTER WAY</div>

  <section class="value v1">
    <h2>Everyone comes back to<br>the <em>Green Zone.</em></h2>
    <p><span class="lbl">WHAT IT MEANS</span> - Safety takes precedence over every phase of the day's operation.</p>
    <p><span class="lbl">HOW TO EXPRESS IT</span> - Anyone can call a stop to the work in progress if an unsafe act is occurring. In fact, it is each team member's duty to do so, rectify the unsafe issue, then proceed. Never hesitate; everyone comes back. Finally, each After Action Review begins with discussing safety issues.</p>
    <p>We always let everyone on the team know of an unsafe situation, so it can be avoided in the future.</p>
    <div class="float-r" style="width:92px;height:44px"></div>
    <p><span class="lbl">RESULT</span> - All team members go home to their loved ones each day to pursue their individual happiness.</p>
  </section>

  <section class="value v2">
    <h2>Boldly go. <em>Seek.</em> Find.</h2>
    <p><span class="lbl">WHAT IT MEANS:</span> - We weave innovation into the fabric that makes up our company.</p>
    <p><span class="lbl">HOW TO EXPRESS IT:</span> - We're early adopters of technology. We quickly evaluate new technologies or processes that could separate us from our competition. Then we implement and evaluate these new technologies. We dump it quickly if we see it is not helping us achieve "Commander's Intent." We have the guts to be first. We iterate continuously and attack, attack, attack.</p>
    <p style="padding-left:60px"><span class="lbl">RESULT:</span> - We will be ahead of our competition. It' one mechanism that helps us scale. Prosperity favors the bold!</p>
  </section>

  <section class="value v3">
    <h2>Never leave your<br>wingman</h2>
    <div class="float-r" style="width:190px;height:118px"></div>
    <p><span class="lbl">WHAT IT MEANS</span> – We always help your team members be successful. Commitment to each other and to our own personal integrity is the fuel that empowers us.</p>
    <p class="gap"><span class="lbl">HOW TO EXPRESS IT</span> – If a Wingman is having challenges accomplishing their individual priorities or completing their assigned mission, volunteer to help them to do so.</p>
    <p class="gap">This goes for Subs/Suppliers as well. We help those who help us succeed! Always look to establish the best win-win relationship possible, and do what you can to support them if they get into a bind.</p>
    <p class="gap"><span class="lbl">RESULT</span> – Be there for them and they will be there for us.</p>
  </section>

  <section class="value v4">
    <h2>Fail quickly and learn</h2>
    <p><span class="lbl">WHAT IT MEANS</span> – If you're not making mistakes, you're not taking enough chances or getting out of your comfort zone.</p>
    <p class="gap"><span class="lbl">HOW TO EXPRESS IT</span> – Use your best judgment when trying something new. But, don't let your pride keep you from saying, "I was wrong" when your idea doesn't work. We trust you will know when it's time to dump the idea, or stop doing something that doesn't work.</p>
    <p class="gap">RESULT – No one will ever be penalized for making a mistake. Don't be afraid to try something you believe will work. That's how we grow ourselves and our team members.</p>
    <p class="gap"><span class="lbl">RESULT</span> – Be there for them and they will be there for us.</p>
  </section>

  <section class="value v5">
    <h2>Troops (Team Members) <span style="color:var(--maroon)">eat first</span></h2>
    <p><span class="lbl">WHAT IT MEANS</span> – No leader will put themselves ahead of their subordinates.</p>
    <p><span class="lbl">HOW TO EXPRESS IT</span> – We lead by example. Demonstrate the moral courage and discipline to do the right thing at the highest level of quality.</p>
    <p><span class="lbl">RESULT</span> – Every new teammember's will quickly realize their leaders genuinely care for their welfare and success. This is the best way to drive Esprit de Corps and achieve excellence.</p>
  </section>

  <div class="emblem">CORE<br>VALUES</div>
  <svg class="sweep" viewBox="0 0 674 953">
    <defs>
      <linearGradient id="handTone" x1="0" y1="0" x2="1" y2="0">
        <stop offset="0" stop-color="#6a0f20"/>
        <stop offset="0.6" stop-color="#b01c38"/>
        <stop offset="1" stop-color="#8a1428"/>
      </linearGradient>
    </defs>
    <path d="M418 600 C480 572 570 560 633 564 L633 630 C560 620 480 614 418 612 Z" fill="#c8cad6" opacity="0.3"/>
    <path d="M635 562 C650 564 662 567 674 570 L674 646 C662 641 648 636 635 633 Z" fill="var(--navy)"/>
    <g role="img" aria-label="Open hand illustration reaching toward the core values emblem">
      <path d="M200 500 C240 495 275 515 300 535 C340 528 380 528 418 530 L418 580 C380 592 350 605 320 606 C285 600 255 575 235 550 C220 535 208 520 200 500 Z" fill="url(#handTone)"/>
    </g>
  </svg>

  <footer class="footer">www.keystoneaid7.example</footer>
</main>
</body>
</html>
```